KR Appraisals website redesign

I would like to refresh my existing website of www.krappraisals-example.com with new graphics, look and feel, as well as updated structure and wording. Content and layout changes have been uploaded to this project Brief.

My existing website has a dark feel. I am now looking for a light and energetic feel. Financial Services is my industry, so the website should be reflect that. I would also like to reflect the concepts of Trust, Service and Expertise.

The website must be serious and upmarket.

Target Market(s)

Corporate board members, CFO's, treasurers and controllers
Auditors, tax advisors, private equity and venture capital asset managers, investors, tax authorities

Industry/Entity Type

Financial Service

Coding

Coded - Design and coding required

Number of Pages Required

5+ page

Font styles to use
Sans Serif
Other font styles liked:
• Designer can choose another modern font

Colors
0355a3
3277b5
85acd3
eaf1f7
f37122
f68d4d
9bcb3c
acd037
cadf82

Requirements
Must have
• Good hi resolution pictures that convey "Finance", "Trust", "Service" or "Expertise".
• An anti-bot (such as Captcha) mechanism in the contact form.
Should not have
• Must not have all content on one rolling screen.

```html
<!DOCTYPE html>
<html lang="en">
<head>
<meta charset="utf-8">
<title>KR Appraisals – Services</title>
<link href="https://fonts.googleapis.com/css2?family=Montserrat:wght@400;500;600;700&display=swap" rel="stylesheet">
<style>
  :root{
    --blue:#0355a3;
    --orange:#f37122;
    --green:#9bcb3c;
    --grey-text:#666;
    --nav-grey:#7a7a7a;
    --panel:#f2f2f2;
    --footer:#333333;
    --footer-text:#9a9a9a;
    --footer-line:#5a5a5a;
    --white:#ffffff;
  }
  *{margin:0;padding:0;box-sizing:border-box}
  html,body{width:1200px;height:1144px;overflow:hidden}
  body{position:relative;background:var(--white);font-family:"Montserrat",sans-serif;color:var(--grey-text)}

  .site-header{position:absolute;left:0;top:0;width:1200px;height:100px;
    background:linear-gradient(90deg,#dedfd2 0%,#ecece0 40%,#f4f4e2 100%)}
  .brand{position:absolute;display:flex;align-items:center;gap:9px;color:#858585;
    font-weight:500;font-size:20px;letter-spacing:.5px}
  .brand-mark{width:14px;height:14px;background:#858585}
  .site-header .brand{left:161px;top:38px}

  .main-nav{position:absolute;top:45px;left:0;height:14px;font-size:11px;font-weight:600;letter-spacing:.2px}
  .main-nav a{position:absolute;white-space:nowrap;color:var(--nav-grey);text-decoration:none}
  .main-nav a.active{color:var(--blue)}

  .page-title{position:absolute;left:0;width:1200px;top:185px;text-align:center;
    color:var(--orange);font-weight:700;font-size:37px;letter-spacing:-.5px}

  .service-panel{position:absolute;left:562px;top:281px;width:477px;height:420px;background:var(--panel)}
  .service-photo{position:absolute;left:161px;top:341px;width:439px;height:293px;
    background:linear-gradient(135deg,#2b3440 0%,#7f93a8 35%,#dfe6ee 55%,#8a7c72 80%,#3a3330 100%)}
  .service-title{position:absolute;left:639px;top:388px;color:var(--green);font-weight:700;
    font-size:31px;line-height:37.5px;letter-spacing:-.2px}
  .service-text{position:absolute;left:639px;top:486px;width:370px;font-size:10.4px;line-height:18.75px;color:var(--grey-text)}

  .site-footer{position:absolute;left:0;top:791px;width:1200px;height:353px}
  .footer-shape{position:absolute;left:0;top:0}
  .site-footer .brand{left:0;width:1200px;justify-content:center;top:64px;color:#8a8a8a;font-size:22px}
  .site-footer .brand-mark{background:#8a8a8a}
  .footer-rule{position:absolute;left:161px;width:879px;height:1px;background:var(--footer-line)}
  .footer-nav{top:161px}
  .footer-nav a{color:var(--footer-text)}
  .footer-nav a.active{color:var(--green)}

  .footer-col{position:absolute;top:224px;font-size:10.4px;line-height:22.5px;color:var(--footer-text)}
  .footer-col h3{font-size:13.5px;font-weight:600;color:var(--orange);margin-bottom:8px;line-height:18px}
  .footer-col .accent{color:var(--green)}
  .footer-col .bright{color:var(--white)}
  .contact-line{display:flex;gap:8px;align-items:flex-start;line-height:16.5px}
  .contact-line svg{flex:none;margin-top:2px}
  .contact-line.phone{margin-top:13px;color:var(--white);font-size:11px;font-weight:500}

  .badge{position:absolute;background:#5a5a5a;border-radius:4px}
</style>
</head>
<body>

<header class="site-header">
  <div class="brand"><span class="brand-mark"></span>KR Appraisals</div>
  <nav class="main-nav">
    <a style="left:611px">HOME</a>
    <a style="left:686px">ABOUT</a>
    <a class="active" style="left:766px">SERVICES</a>
    <a style="left:861px">NEWS &amp; VIEWS</a>
    <a style="left:985px">CONTACT</a>
  </nav>
</header>

<h1 class="page-title">OUR SERVICES</h1>

<section class="service">
  <div class="service-panel"></div>
  <div class="service-photo" role="img" aria-label="Low-angle view of glass office towers against a cloudy sky"></div>
  <h2 class="service-title">INTELLECTUAL<br>PROPERTY VALUATION</h2>
  <p class="service-text">Patents, unpatented technologies, know how, brands, trademarks, databases, customer-related assets - this is a limited sample of the wide universe of intellectual property that clients trust KR Appraisals to value. There are many techniques for valuing intellectual property and no two assets are alike. Trust KR Appraisals for our expertise and client-centric approach.</p>
</section>

<footer class="site-footer">
  <svg class="footer-shape" width="1200" height="353" viewBox="0 0 1200 353" aria-hidden="true">
    <polygon points="0,68 600,0 1200,68 1200,353 0,353" fill="var(--footer)"/>
  </svg>
  <div class="brand"><span class="brand-mark"></span>KR Appraisals</div>
  <div class="footer-rule" style="top:145px"></div>
  <nav class="main-nav footer-nav">
    <a class="active" style="left:386px">HOME</a>
    <a style="left:461px">ABOUT</a>
    <a style="left:541px">SERVICES</a>
    <a style="left:636px">NEWS &amp; VIEWS</a>
    <a style="left:760px">CONTACT</a>
  </nav>
  <div class="footer-rule" style="top:190px"></div>

  <div class="footer-col" style="left:163px">
    <h3>CREDITS</h3>
    <div>© 2019 <span class="accent">KR Appraisals</span></div>
    <div>Logo by <span class="bright">Mara Delvane</span></div>
    <div>Website by <span class="accent">Brightline Webworks</span></div>
  </div>

  <div class="footer-col" style="left:389px">
    <h3>LEIDEN</h3>
    <div class="contact-line">
      <svg width="10" height="13" viewBox="0 0 10 13"><path d="M5 0a5 5 0 0 0-5 5c0 3.5 5 8 5 8s5-4.5 5-8a5 5 0 0 0-5-5zm0 7a2 2 0 1 1 0-4 2 2 0 0 1 0 4z" fill="var(--green)"/></svg>
      <div>Havenstraat 14<br>2311 AB Leiden</div>
    </div>
    <div class="contact-line phone">
      <svg width="12" height="12" viewBox="0 0 12 12"><path d="M2.4 0.5l2 2.4-1.1 1.6c.8 1.7 2.1 3 3.8 3.8l1.6-1.1 2.4 2-1.3 2.1C5 11 1 7 .3 1.8z" fill="var(--green)"/></svg>
      <div>070 555 0142</div>
    </div>
  </div>

  <div class="footer-col" style="left:617px">
    <h3>AMSTERDAM</h3>
    <div class="contact-line">
      <svg width="10" height="13" viewBox="0 0 10 13"><path d="M5 0a5 5 0 0 0-5 5c0 3.5 5 8 5 8s5-4.5 5-8a5 5 0 0 0-5-5zm0 7a2 2 0 1 1 0-4 2 2 0 0 1 0 4z" fill="var(--green)"/></svg>
      <div>Keizerskade 8<br>1017 XY Amsterdam</div>
    </div>
    <div class="contact-line phone">
      <svg width="12" height="12" viewBox="0 0 12 12"><path d="M2.4 0.5l2 2.4-1.1 1.6c.8 1.7 2.1 3 3.8 3.8l1.6-1.1 2.4 2-1.3 2.1C5 11 1 7 .3 1.8z" fill="var(--green)"/></svg>
      <div>020 555 0187</div>
    </div>
  </div>

  <div class="badge" style="left:856px;top:210px;width:170px;height:38px" role="img" aria-label="Professional institute membership badge"></div>
  <div class="badge" style="left:855px;top:257px;width:170px;height:70px" role="img" aria-label="Appraisers society membership badge"></div>
</footer>

</body>
</html>
```